Brand Identity Stationary Package

Hello I'm looking for a full branding package for my Property Management Company. I have a logo but looking to have the following
Business Card
Email signature
Facebook cover photo
Letterhead (word.doc)
#10 Envelope
Pocket Folder - link to 9x12 pocket folder design specs https://www.printorbit-example.ca/marketing-materials/presentation-folders
would like everything to match and be brand identifiable. The company looks after residential properties/apartments and some commercial properties. Attached is a zip of the files.
For Business Card
Name: Gareth Lindqvist
Position: Operations Manager
Number: 1 (555) 384-2917
Email: Gareth@harborkey-example.ca
Website: Harborkey-example.ca
Property Management

```html
<!DOCTYPE html>
<html lang="en">
<head>
<meta charset="utf-8">
<title>Harborkey Property Management – #10 Envelope</title>
<link rel="stylesheet" href="https://fonts.googleapis.com/css2?family=Montserrat:wght@500;700&family=Source+Sans+3:wght@400&display=swap">
<style>
  :root {
    --backdrop: #d0d0d0;
    --brand-green: #80a642;
    --ink: #111111;
    --paper: #f1f0f0;
    --paper-light: #ffffff;
  }
  html, body {
    margin: 0;
    padding: 0;
    overflow: hidden;
  }
  body {
    width: 1200px;
    height: 1050px;
    background: var(--backdrop);
    position: relative;
  }
  .envelope {
    position: absolute;
    left: 145px;
    width: 910px;
    height: 390px;
    display: block;
  }
  .envelope--back { top: 105px; }
  .envelope--front { top: 555px; }
  .wordmark {
    font-family: "Montserrat", sans-serif;
    font-weight: 700;
  }
  .tagline {
    font-family: "Montserrat", sans-serif;
    font-weight: 500;
  }
  .contact-text {
    font-family: "Source Sans 3", sans-serif;
    font-weight: 400;
    fill: var(--ink);
  }
</style>
</head>
<body>

<svg class="envelope envelope--back" viewBox="0 0 910 390" aria-label="Envelope back with flap">
  <defs>
    <radialGradient id="paper-glow-back" cx="0.5" cy="0.65" r="0.6">
      <stop offset="0" stop-color="var(--paper-light)"/>
      <stop offset="1" stop-color="var(--paper)"/>
    </radialGradient>
  </defs>
  <rect class="envelope-body" width="910" height="390" fill="url(#paper-glow-back)"/>
  <path class="envelope-flap" fill="var(--brand-green)"
        d="M0 0 H910 L885 88 Q870 131 835 131 H75 Q40 131 25 88 Z"/>
  <text class="wordmark" x="455" y="70" text-anchor="middle" font-size="47"
        textLength="306" lengthAdjust="spacingAndGlyphs" fill="#f4f4f4">HARBORKEY</text>
  <text class="tagline" x="455" y="89" text-anchor="middle" font-size="10.5"
        textLength="306" lengthAdjust="spacing" fill="#f4f4f4">PROPERTY MANAGEMENT</text>
</svg>

<svg class="envelope envelope--front" viewBox="0 0 910 390" aria-label="Envelope front with return address">
  <defs>
    <radialGradient id="paper-glow-front" cx="0.5" cy="0.3" r="0.6">
      <stop offset="0" stop-color="var(--paper-light)"/>
      <stop offset="1" stop-color="var(--paper)"/>
    </radialGradient>
  </defs>
  <rect class="envelope-body" width="910" height="390" fill="url(#paper-glow-front)"/>

  <path class="wave wave--top" fill="var(--brand-green)"
        d="M0 0 H910 V80 C840 58 780 57 737 58 C560 60 400 88 229 88 C120 88 50 78 0 61 Z"/>
  <path class="swoosh swoosh--top" fill="var(--ink)"
        d="M513 75 C620 67 700 65 760 66 C830 67 870 76 910 89 V100 C860 84 820 76 760 72 C690 70 600 72 513 75 Z"/>

  <path class="wave wave--bottom" fill="var(--brand-green)"
        d="M0 327 C50 345 100 352 160 352 C350 352 560 319 734 319 C820 319 870 333 910 346 V390 H0 Z"/>
  <path class="swoosh swoosh--bottom" fill="var(--ink)"
        d="M0 302 C60 325 140 338 230 340 C300 341 350 340 394 339 C330 342 280 346 220 346 C130 346 60 330 0 313 Z"/>

  <text class="wordmark" x="52" y="165" font-size="37"
        textLength="257" lengthAdjust="spacingAndGlyphs" fill="var(--ink)">HARBORKEY</text>
  <text class="tagline" x="52" y="182" font-size="9"
        textLength="257" lengthAdjust="spacing" fill="var(--ink)">PROPERTY MANAGEMENT</text>

  <g class="contact contact--phone">
    <path fill="var(--brand-green)" d="M52 228 Q59 221 66 228 L65 231 L62 231 L61 229 L57 229 L56 231 L53 231 Z M55 232 H63 L65 239 H53 Z"/>
    <text class="contact-text" x="80" y="238" font-size="19">1 (555) 384-2917</text>
  </g>
  <g class="contact contact--email">
    <rect x="52" y="253" width="15" height="10" fill="var(--brand-green)"/>
    <path d="M52 253 L59.5 259 L67 253" fill="none" stroke="#f1f0f0" stroke-width="1.2"/>
    <text class="contact-text" x="80" y="264" font-size="19">Gareth@harborkey-example.ca</text>
  </g>
  <g class="contact contact--web">
    <circle cx="59.5" cy="283" r="7.5" fill="var(--brand-green)"/>
    <path d="M52 283 H67 M59.5 275.5 Q55 283 59.5 290.5 M59.5 275.5 Q64 283 59.5 290.5" fill="none" stroke="#f1f0f0" stroke-width="1"/>
    <text class="contact-text" x="80" y="290" font-size="19">www.Harborkey-example.ca</text>
  </g>
</svg>

</body>
</html>
```